Property management company looking for modern card design

We at Blue Heron Partners provides property management services for its residential and commercial properties, with expertise in all categories of multifamily, industrial and office projects throughout California.

We need a business card design that is professional and modern designed business card. In our field, clients get hundreds of business cards, we would like our card to stand out.

Please avoid small print.

Target Market(s)

Professionals and high end clients

Industry/Entity Type

Financial Planning

Contact Information for Business Card

Company Name: Blue Heron Partners, Name, email, license #, phone number, website blueheronpartners.com

Font styles to use
Sans Serif

Requirements
Must have
• The card design needs to be adaptable because there is a possibly we will be expanding into different sectors other than real estate. The card design should be focused on financial planning and asset management.
Nice to have
• Modern and simple business card. Eye catching. Non-standard size/shaped cards would be great.
• blueheronpartners.com
Should not have
• Too many bright color or any pictures or shapes of real estate stuff.

```html
<!DOCTYPE html>
<html lang="en">
<head>
<meta charset="utf-8">
<title>Blue Heron Partners – Business Card</title>
<link href="https://fonts.googleapis.com/css2?family=Open+Sans:wght@400;600;700&display=swap" rel="stylesheet">
<style>
  :root {
    --backdrop: #e9e6e1;
    --card-light: #c4955f;
    --card-mid: #b5834f;
    --card-dark: #a87443;
    --ink: #121212;
    --band-grey: #2b2b2b;
    --band-black: #050505;
    --shadow: rgba(0, 0, 0, 0.28);
  }
  * { margin: 0; padding: 0; box-sizing: border-box; }
  html, body {
    width: 1200px;
    height: 900px;
    overflow: hidden;
    background: var(--backdrop);
    font-family: "Open Sans", Arial, sans-serif;
    color: var(--ink);
  }
  .stage { position: relative; width: 1200px; height: 900px; }
  .card {
    position: absolute;
    width: 600px;
    height: 343px;
    border-radius: 4px;
    overflow: hidden;
    background: linear-gradient(135deg, var(--card-light) 0%, var(--card-mid) 55%, var(--card-dark) 100%);
    box-shadow: 0 10px 26px var(--shadow);
  }
  .card--brand { left: 540px; top: 80px; }
  .card--contact { left: 60px; top: 470px; }

  .wordmark {
    position: absolute;
    display: flex;
    align-items: center;
    gap: 14px;
    font-weight: 400;
    font-size: 38px;
    letter-spacing: 0.5px;
    color: var(--ink);
    white-space: nowrap;
    z-index: 1;
  }
  .wordmark__dot {
    width: 30px; height: 30px;
    border-radius: 50%;
    background: var(--ink);
    flex: none;
  }
  .card--brand .wordmark { left: 50%; top: 50%; transform: translate(-50%, -50%); }
  .card--contact .wordmark { right: 34px; top: 92px; font-size: 32px; gap: 12px; }
  .card--contact .wordmark__dot { width: 26px; height: 26px; }

  .card__bands { position: absolute; inset: 0; width: 100%; height: 100%; }

  .holder { position: absolute; left: 74px; top: 20px; z-index: 1; }
  .holder__name { font-weight: 700; font-size: 19px; line-height: 1.15; }
  .holder__role { font-weight: 400; font-size: 14px; }

  .contact { position: absolute; left: 26px; top: 148px; font-size: 15px; line-height: 1.45; z-index: 1; }
  .contact__license { font-weight: 700; font-size: 16px; margin-left: 20px; margin-bottom: 2px; }
  .contact__license span { font-weight: 400; }
  .contact__row { display: flex; align-items: center; gap: 8px; }
  .contact__row svg { width: 12px; height: 12px; fill: var(--ink); flex: none; }
  .contact__row--plain { padding-left: 20px; }
</style>
</head>
<body>
<main class="stage">

  <section class="card card--brand" aria-label="Card back">
    <div class="wordmark"><span class="wordmark__dot"></span>Blue Heron Partners</div>
  </section>

  <section class="card card--contact" aria-label="Card front">
    <svg class="card__bands" viewBox="0 0 600 343" preserveAspectRatio="none" aria-hidden="true">
      <polygon points="0,22 64,22 42,52 0,52" fill="var(--band-black)"/>
      <polygon points="42,52 64,22 64,52" fill="var(--band-grey)"/>
      <polygon points="0,274 330,274 314,292 0,292" fill="var(--band-grey)"/>
      <polygon points="314,292 330,274 600,274 600,343 262,343" fill="var(--band-black)"/>
    </svg>

    <div class="holder">
      <p class="holder__name">Daniel Whitford</p>
      <p class="holder__role">Managing Director</p>
    </div>

    <div class="wordmark"><span class="wordmark__dot"></span>Blue Heron Partners</div>

    <div class="contact">
      <p class="contact__license">License: <span>BHP01245</span></p>
      <p class="contact__row">
        <svg viewBox="0 0 24 24"><path d="M6.6 10.8a15.1 15.1 0 0 0 6.6 6.6l2.2-2.2a1 1 0 0 1 1-.25 11.4 11.4 0 0 0 3.6.57 1 1 0 0 1 1 1V20a1 1 0 0 1-1 1A17 17 0 0 1 3 4a1 1 0 0 1 1-1h3.5a1 1 0 0 1 1 1c0 1.25.2 2.45.57 3.57a1 1 0 0 1-.25 1z"/></svg>
        044-987 654 321
      </p>
      <p class="contact__row">
        <svg viewBox="0 0 24 24"><path d="M2 5h20v14H2z M2 5l10 8 10-8" /></svg>
        info@heronmail.com
      </p>
      <p class="contact__row">
        <svg viewBox="0 0 24 24"><circle cx="12" cy="12" r="10"/></svg>
        www.heronsite.com
      </p>
      <p class="contact__row contact__row--plain">www.blueheronpartners.com</p>
    </div>
  </section>

</main>
</body>
</html>
```